Namibia currently imports 60% of its food. Harvest Crest Oruva is an initiative which will assist Namibia to become self sustainable in terms of food production. We aim to do this through the development of 3 agricultural production zones which will include farming zones, local farmer assistance, processing and distribution of the final products. Please see our project overview attached.

```html
<!DOCTYPE html>
<html lang="en">
<head>
<meta charset="UTF-8">
<title>Harvest Crest Oruva</title>
<link href="https://fonts.googleapis.com/css2?family=Cinzel:wght@600;700&family=Montserrat:wght@400;500;600&display=swap" rel="stylesheet">
<style>
:root{
  --green:#0b6b37;
  --green-dark:#2a5c44;
  --cream:#f4f3ef;
  --ink:#222;
  --muted:#444;
  --white:#fff;
  --sand:#c7a27a;
}
*{box-sizing:border-box;margin:0;padding:0}
html,body{width:1200px;height:3817px;overflow:hidden}
body{position:relative;background:var(--white);font-family:'Montserrat',sans-serif;color:var(--ink)}
.abs{position:absolute}
.serif{font-family:'Cinzel',serif;font-weight:700}

/* header */
.site-header{left:0;top:0;width:1200px;height:116px;background:var(--white)}
.nav-link{font-size:16px;font-weight:500;top:52px;letter-spacing:.3px}
.brand{left:400px;top:30px;width:400px;text-align:center}
.brand-name{font-family:'Cinzel',serif;font-weight:600;font-size:34px;color:var(--green);line-height:1}
.brand-sub{font-size:12px;letter-spacing:7px;color:var(--sand);margin-top:6px}

/* hero */
.hero-photo{left:0;top:116px;width:1200px;height:552px;background:linear-gradient(180deg,#c9d9c4 0%,#9cc07f 45%,#5f9b3d 100%)}
.hero-circle{left:696px;top:166px;width:454px;height:454px;border-radius:50%;background:var(--green);color:var(--white);text-align:center;padding-top:108px}
.hero-title{font-size:40px;line-height:68px}
.hero-sub{font-size:20px;font-weight:600;line-height:48px;margin-top:8px}

/* services */
.services{left:0;top:668px;width:1200px;height:726px;background:var(--green);color:var(--white)}
.section-title{width:1200px;text-align:center;font-size:42px}
.service{width:330px;text-align:center}
.service-icon{width:72px;height:72px;border-radius:50%;background:var(--white);margin:0 auto;display:flex;align-items:center;justify-content:center}
.service-label{font-size:20px;font-weight:600;margin-top:34px;letter-spacing:.3px}
.service.active{background:var(--white);color:var(--green);border-radius:4px}
.service.active .service-icon{background:var(--green)}
.btn{border:1.5px solid currentColor;border-radius:28px;display:flex;align-items:center;justify-content:center;font-size:19px;font-weight:500;width:161px;height:52px}

/* about */
.photo-main{left:221px;top:1493px;width:333px;height:506px;border-radius:6px;background:linear-gradient(160deg,#5b7a36,#2f5a26 60%,#3e7a2e)}
.photo-small{left:130px;top:1870px;width:332px;height:243px;border-radius:6px;background:linear-gradient(180deg,#4e6a34,#3a3229)}
.about-title{left:610px;top:1595px;font-size:42px;color:var(--green);line-height:60px}
.about-text{left:610px;top:1736px;width:520px;font-size:15px;line-height:36px;color:var(--muted)}

/* solution */
.solution-band{left:0;top:2213px;width:1200px;height:407px;background:var(--cream)}
.region{top:2422px;width:310px;height:422px;border-radius:6px;overflow:hidden;background:var(--green)}
.region-photo{height:329px}
.region-label{color:var(--white);text-align:center;font-size:19px;font-weight:600;line-height:38px;padding-top:16px}

/* contact */
.field{height:40px;border-bottom:1.5px solid #555;font-size:16px;font-weight:600;display:flex;justify-content:space-between;align-items:flex-start}

/* footer */
.site-footer{left:0;top:3452px;width:1200px;height:365px;background:var(--green-dark);color:var(--white)}
.social{width:30px;height:30px;border-radius:50%;background:var(--white)}
.foot-link{font-size:17px;font-weight:600;top:226px}
</style>
</head>
<body>

<header class="abs site-header">
  <span class="abs nav-link" style="left:165px">HOME</span>
  <span class="abs nav-link" style="left:268px">ABOUT US</span>
  <div class="abs brand">
    <div class="brand-name">HARVEST CREST</div>
    <div class="brand-sub">ORUVA</div>
  </div>
  <span class="abs nav-link" style="left:800px">SERVICES</span>
  <span class="abs nav-link" style="left:933px">CONTACT US</span>
</header>

<div class="abs hero-photo" role="img" aria-label="Young farmer holding a tablet in a green leafy crop field"></div>
<div class="abs hero-circle">
  <div class="serif hero-title">HARVEST CREST<br>ORUVA</div>
  <div class="hero-sub">AN ORV AGRI-TECH, FOOD SECURITY<br>INITIATIVE</div>
</div>

<section class="abs services">
  <h2 class="abs serif section-title" style="top:80px">OUR SERVICES</h2>

  <div class="abs service" style="left:82px;top:222px">
    <div class="service-icon"><svg width="38" height="38" viewBox="0 0 38 38" fill="none" stroke="#0b6b37" stroke-width="2"><path d="M6 30h26M12 30V16M19 30V10M26 30V18"/><path d="M12 16c-3-1-4-4-4-6 3 0 4 3 4 6zM19 10c3-1 4-4 4-6-3 0-4 3-4 6z"/></svg></div>
    <div class="service-label">CROP MANAGEMENT</div>
  </div>
  <div class="abs service active" style="left:443px;top:196px;width:264px;height:167px;padding-top:26px">
    <div class="service-icon"><svg width="38" height="38" viewBox="0 0 38 38" fill="none" stroke="#fff" stroke-width="2"><circle cx="19" cy="12" r="6"/><path d="M8 32c0-7 5-11 11-11s11 4 11 11"/></svg></div>
    <div class="service-label">FARM MANAGEMENT</div>
  </div>
  <div class="abs service" style="left:766px;top:222px">
    <div class="service-icon"><svg width="38" height="38" viewBox="0 0 38 38" fill="none" stroke="#0b6b37" stroke-width="2"><path d="M19 32V16M19 16c-6 0-9-4-9-8 5 0 9 3 9 8zM19 20c5 0 8-3 8-7-4 0-8 3-8 7M8 32h22"/></svg></div>
    <div class="service-label">SOIL HEALTH &amp; IRRIGATION</div>
  </div>

  <div class="abs service" style="left:82px;top:410px">
    <div class="service-icon"><svg width="38" height="38" viewBox="0 0 38 38" fill="none" stroke="#0b6b37" stroke-width="2"><circle cx="19" cy="12" r="5"/><path d="M6 26l8-5 5 3 5-3 8 5M10 30l9 3 9-3"/></svg></div>
    <div class="service-label">BUSINESS MANAGEMENT</div>
  </div>
  <div class="abs service" style="left:410px;top:410px">
    <div class="service-icon"><svg width="38" height="38" viewBox="0 0 38 38" fill="none" stroke="#0b6b37" stroke-width="2"><path d="M8 16h5l12-7v20l-12-7H8zM13 22l2 8h4M29 14l4-2M29 19h4"/></svg></div>
    <div class="service-label">MARKETING</div>
  </div>
  <div class="abs service" style="left:766px;top:410px">
    <div class="service-icon"><svg width="38" height="38" viewBox="0 0 38 38" fill="none" stroke="#0b6b37" stroke-width="2"><rect x="16" y="8" width="14" height="12"/><path d="M6 26h8l6 3h10M6 32h24"/></svg></div>
    <div class="service-label">LOGISTICS MANAGEMENT</div>
  </div>

  <div class="abs btn" style="left:519px;top:593px;color:var(--white)">VIEW MORE</div>
</section>

<div class="abs photo-small" role="img" aria-label="Hands planting a seedling in dark soil"></div>
<div class="abs photo-main" role="img" aria-label="Smiling farmer in a straw hat holding fresh leafy greens"></div>
<h2 class="abs serif about-title">NAMIBIA NEEDS<br>FOOD</h2>
<p class="abs about-text">Namibia is a young democracy in Sub-Saharan Africa with a population of approximately 2.5 Million people. The country's agricultural sector has been slow to keep up with the increasing population. As a consequence, approximately 60% of the food required to feed the nation is imported. The elevated cost of these imported foods means a large proportion of the population consume food with low nutritional value.</p>
<div class="abs btn" style="left:610px;top:2015px;color:var(--green)">VIEW MORE</div>

<div class="abs solution-band"></div>
<h2 class="abs serif section-title" style="left:0;top:2290px;color:var(--green)">HARVEST CREST SOLUTION</h2>

<div class="abs region" style="left:111px">
  <div class="region-photo" role="img" aria-label="Aerial view of a town with red roofs" style="background:linear-gradient(180deg,#8fb5e0 0%,#c9d8e4 28%,#b06a4a 55%,#4e6e3a 100%)"></div>
  <div class="region-label">OTAVI REGION<br>CENTRAL NAMIBIA</div>
</div>
<div class="abs region" style="left:446px">
  <div class="region-photo" role="img" aria-label="Wide river with dry riverbanks and trees" style="background:linear-gradient(180deg,#dfe8ec 0%,#c7c4b4 40%,#6f7560 62%,#3f4a36 100%)"></div>
  <div class="region-label">KAVANGO REGION<br>NORTH NAMIBIA</div>
</div>
<div class="abs region" style="left:779px">
  <div class="region-photo" role="img" aria-label="Large concrete dam wall in a rocky canyon" style="background:linear-gradient(180deg,#3d6fa8 0%,#8a5a40 25%,#c8c6c0 55%,#a5a29a 80%,#7a6a55 100%)"></div>
  <div class="region-label">NECKARTAL DAM<br>SOUTH NAMIBIA</div>
</div>

<h2 class="abs serif section-title" style="left:0;top:2956px;color:var(--green)">CONTACT US</h2>
<div class="abs field" style="left:132px;top:3058px;width:444px"><span>FIRST NAME</span><svg width="14" height="14" viewBox="0 0 14 14"><circle cx="7" cy="4" r="3.2" fill="#222"/><path d="M1 14c0-4 3-6 6-6s6 2 6 6z" fill="#222"/></svg></div>
<div class="abs field" style="left:624px;top:3058px;width:444px"><span>LAST NAME</span><svg width="14" height="14" viewBox="0 0 14 14"><circle cx="7" cy="4" r="3.2" fill="#222"/><path d="M1 14c0-4 3-6 6-6s6 2 6 6z" fill="#222"/></svg></div>
<div class="abs field" style="left:132px;top:3126px;width:444px"><span>EMAIL ADDRESS</span><svg width="16" height="12" viewBox="0 0 16 12"><rect width="16" height="12" fill="#222"/><path d="M0 0l8 6 8-6" stroke="#fff" fill="none"/></svg></div>
<div class="abs field" style="left:624px;top:3126px;width:444px"><span>PHONE NUMBER</span><svg width="13" height="13" viewBox="0 0 13 13"><path d="M2 0l3 3-1.5 2a8 8 0 0 0 4.5 4.5L10 8l3 3-2 2C5 13 0 8 0 2z" fill="#222"/></svg></div>
<div class="abs field" style="left:132px;top:3194px;width:936px;height:56px"><span>TYPE YOUR MESSAGE</span><svg width="14" height="13" viewBox="0 0 14 13"><ellipse cx="7" cy="5.5" rx="7" ry="5.5" fill="#222"/><path d="M2 9l-1 4 4-2z" fill="#222"/></svg></div>
<div class="abs btn" style="left:519px;top:3304px;color:var(--green)">SEND NOW</div>

<footer class="abs site-footer">
  <span class="abs" style="left:111px;top:120px;font-size:26px;font-weight:500">FOLLOW US</span>
  <div class="abs social" style="left:303px;top:120px"></div>
  <div class="abs social" style="left:344px;top:120px"></div>
  <div class="abs social" style="left:385px;top:120px"></div>
  <div class="abs social" style="left:426px;top:120px"></div>
  <span class="abs" style="left:520px;top:112px;width:160px;text-align:center;font-family:'Cinzel',serif;font-weight:600;font-size:38px;color:#cfd8d2">HCO</span>
  <div class="abs" style="left:785px;top:115px;width:304px;height:41px;border:1.5px solid var(--white);display:flex;align-items:center;justify-content:space-between;padding:0 18px;font-size:11px">
    <span>ENTER EMAIL</span>
    <svg width="14" height="12" viewBox="0 0 14 12"><path d="M0 5L14 0 10 12 7 7z" fill="#fff"/></svg>
  </div>
  <span class="abs foot-link" style="left:220px">HOME</span>
  <span class="abs foot-link" style="left:317px">|</span>
  <span class="abs foot-link" style="left:368px">ABOUT</span>
  <span class="abs foot-link" style="left:474px">|</span>
  <span class="abs foot-link" style="left:522px">SERVICES</span>
  <span class="abs foot-link" style="left:652px">|</span>
  <span class="abs foot-link" style="left:700px">SOLUTIONS</span>
  <span class="abs foot-link" style="left:846px">|</span>
  <span class="abs foot-link" style="left:894px">CONTACT</span>
  <span class="abs" style="left:0;top:288px;width:1200px;text-align:center;font-size:17px;font-weight:600">@2024 COPYRIGHTS - HCO - ALL RIGHTS RESERVED</span>
</footer>

</body>
</html>
```